Kelvor Engineers: Why you should hire us keepsake

New design. Open to plastic cards. We are an engineering firm that designs cell phone towers and commercial buildings. Please check out our website www.kelvorstruct.com for more details. We want people to remember our card and for it to be useful if possible. We want the same look and feel on these cards to be translated to other marketing material we may need such as brochures.

Target Market(s)

Architects, Developers and Telecommunication Carriers

Industry/Entity Type

Engineering

Contact Information for Business Card

Card with our company colors, logo, and innovative design with elements related to our industry.

Font styles to use
Sans Serif

Colors
9bcb3c
abd036
0255a3

Requirements
Must have
• Sleek and hip design
Nice to have
• Bright lime green and navy coloring that pops with an innovative design.
Should not have
• A basic and boring design

```html
<!DOCTYPE html>
<html lang="en">
<head>
<meta charset="utf-8">
<title>Kelvor Engineers – Business Card</title>
<link href="https://fonts.googleapis.com/css2?family=Montserrat:wght@400;500;600;800&family=Oswald:wght@600&display=swap" rel="stylesheet">
<style>
  :root {
    --lime: #d2d42b;
    --navy: #1c3461;
    --white: #ffffff;
    --backdrop: #ececec;
    --card-w: 720px;
    --card-h: 411px;
    --radius: 26px;
  }
  * { box-sizing: border-box; margin: 0; padding: 0; }
  html, body { width: 1200px; height: 930px; overflow: hidden; }
  body {
    background: var(--backdrop);
    font-family: "Montserrat", sans-serif;
    display: flex;
    flex-direction: column;
    align-items: center;
    justify-content: center;
    gap: 36px;
  }
  .card {
    position: relative;
    width: var(--card-w);
    height: var(--card-h);
    border-radius: var(--radius);
    overflow: hidden;
    box-shadow: 0 6px 18px rgba(0,0,0,.18);
  }

  /* Front */
  .card-front { background: var(--lime); color: var(--white); }
  .card-front .wordmark {
    position: absolute;
    left: 0; right: 0; top: 118px;
    text-align: center;
    font-weight: 800;
    font-size: 112px;
    letter-spacing: -2px;
    line-height: 1;
  }
  .card-front .offices {
    position: absolute;
    left: 0; right: 0; bottom: 58px;
    text-align: center;
    font-weight: 500;
    font-size: 19px;
    letter-spacing: 2px;
    text-transform: uppercase;
  }
  .offices .sep { margin: 0 10px; opacity: .9; }

  /* Back */
  .card-back { background: var(--white); }
  .card-back .swoosh { position: absolute; inset: 0; width: 100%; height: 100%; }
  .card-back .wordmark {
    position: absolute;
    left: 0; right: 0; top: 46px;
    text-align: center;
    font-weight: 800;
    font-size: 84px;
    letter-spacing: -2px;
    line-height: 1;
    color: var(--lime);
  }
  .card-back .tagline {
    position: absolute;
    left: 0; right: 0; top: 146px;
    text-align: center;
    font-weight: 600;
    font-size: 17px;
    letter-spacing: 1.5px;
    text-transform: uppercase;
    color: var(--navy);
  }
  .holder {
    position: absolute;
    left: 40px; top: 312px;
    width: 270px;
    text-align: right;
  }
  .holder .name {
    font-family: "Oswald", sans-serif;
    font-weight: 600;
    font-size: 30px;
    letter-spacing: .5px;
    text-transform: uppercase;
    color: var(--white);
    line-height: 1.1;
  }
  .holder .role { font-size: 16px; color: var(--lime); }
  .divider {
    position: absolute;
    left: 332px; top: 286px;
    width: 1px; height: 96px;
    background: rgba(255,255,255,.7);
  }
  .contacts {
    position: absolute;
    left: 352px; top: 284px;
    list-style: none;
    color: var(--white);
    font-size: 15px;
  }
  .contacts li { display: flex; align-items: center; gap: 12px; height: 25px; }
  .contacts svg { width: 13px; height: 13px; flex: none; }
</style>
</head>
<body>

  <section class="card card-front" aria-label="Card front">
    <div class="wordmark">Kelvor</div>
    <p class="offices">Denver<span class="sep">|</span>Raleigh<span class="sep">|</span>Tampa<span class="sep">|</span>Phoenix</p>
  </section>

  <section class="card card-back" aria-label="Card back">
    <svg class="swoosh" viewBox="0 0 720 411" preserveAspectRatio="none" aria-hidden="true">
      <path d="M0,198 C300,240 600,206 720,84 L720,411 L0,411 Z" fill="var(--navy)"/>
      <path d="M0,214 C310,256 610,224 720,114 L720,411 L0,411 Z" fill="var(--lime)"/>
      <path d="M0,300 C260,286 540,252 720,156 L720,411 L0,411 Z" fill="var(--navy)"/>
    </svg>

    <div class="wordmark">Kelvor</div>
    <p class="tagline">Multi-Discipline Engineering</p>

    <div class="holder">
      <p class="name">Dana Wrenfield</p>
      <p class="role">Director</p>
    </div>

    <div class="divider"></div>

    <ul class="contacts">
      <li>
        <svg viewBox="0 0 16 16"><path fill="var(--lime)" d="M3 1l3 3-2 2c1 2 4 5 6 6l2-2 3 3-2 2C7 15 1 9 1 3z"/></svg>
        555.014.7731
      </li>
      <li>
        <svg viewBox="0 0 16 16"><rect x="4" y="1" width="8" height="14" rx="1.5" fill="none" stroke="var(--lime)" stroke-width="2"/></svg>
        555.019.3064
      </li>
      <li>
        <svg viewBox="0 0 16 16"><rect x="1" y="3" width="14" height="10" fill="none" stroke="var(--lime)" stroke-width="2"/><path d="M1 3l7 6 7-6" fill="none" stroke="var(--lime)" stroke-width="2"/></svg>
        dwrenfield@kelvorstruct.com
      </li>
      <li>
        <svg viewBox="0 0 16 16"><circle cx="8" cy="8" r="7" fill="var(--lime)"/><path d="M1 8h14M8 1c-3 4-3 10 0 14M8 1c3 4 3 10 0 14" fill="none" stroke="var(--navy)" stroke-width="1"/></svg>
        www.kelvorstruct.com
      </li>
    </ul>
  </section>

</body>
</html>
```